Blood Testing Health App

We are looking for a graphics designer to create a web app for us so that we may insert it into a health management website system.
For branding purposes we are at www.Vantiqor.com and we are revamping our website... Example of new colors attached.
How we work...
We are a blood testing company based in the USA.
We offer a blood testing service nationwide in the USA.
We allow customers to order tests directly from us, visit a lab, have their blood drawn, or submit a urine sample, the lab tests it and they send the results back to our computer system and we share it with the customer.
The benefits of this are the customer does not need to go to the doctor and pay for the doctors visit to order these tests, which save them money. The tests are cheaper than going through the doctor. The customer simply uses us to get the test and the results and they can then take the results to their doctor... this process has saved them money. Others may be interested in regular check ups for blood work etc... and this allows them to do it with out needing a doctor, or if you have no insurance, this is a cheaper option too. We are quicker than a doctor, customers do not need appointments etc.
Hopefully you now have a better understanding as to what we do.
Here is the spec.
The app screen size is 750 px wide by 700 px high. ( A pdf is attached to show where the app is going to go, it is on page 3 of the pdf) The customer will have the ability to scroll… therefore the length of the page can be longer.
The app will consist of the following sections
Entry Page –
This will be the first page the user sees upon opening the app. This will be where they are directed from to the sections of the app discussed below. This needs to be branded for VantiQor with a modern look.
1 – Order Test (Giving them the ability to purchase a blood test within the app)
2 – VantiQor Dashboard (A dashboard that has everything they could need to use our service_
How it works Section on entry page – this will be a simple set of graphics showing how the service works. We already have the graphics for this, they do not need to be built again. They are attached to this brief
Basic structure of sections –
Order Test –
This page contains all tests, filed in categories – and Sub categories – Each test needs a link to an Information section – Price – Buy Now – Cart Process
VantiQor Dashboard –
A page of icons along the top of the app
- My Confirmation
- My Nearest Lab
- My Receipt
- My Orders
- My Account
- My Results
- My Inbox
- Contact Us
Sections in more detail -
Order A Test –
Show all categories/ sub categories – There are 23 categories, 14 sub categories, and within these categories are 300 tests - Here is the information for the categories etc - http://www.vantiqor.com/panels.aspx?PanelGroupID=4 Just in case it helps :)
We need to present this in a graphic format that is spacious, modern (brimlake, kivvo web appearance is the direction we are going for) We need it to be clear and not overwhelming to the customer.
Functionality idea…
Customer clicks category/ subcategory and tests appear.
Customer sees small 35 word description. For more information the test opens into a lightbox or expand the container which ever graphic designer believes to be most visually appealing
Buy Now must always be visible, along with price of the test
Buying process explained – Customer clicks buy now –
They are then taken to a Review Order screen ( This contains Order summary and choose payment method – insert payment details )
– Confirm payment –
Confirmation screen appears, thanking them.
They are then taken to the VantiQor Dashboard...
VantiQor Dashboard –
"My Confirmation" - Print Confirmation Order (PDF is in brief, we want this web based not a pdf download)
"My Nearest Lab Location" - This does not need to be designed because the web developer has this part under control, but we do need the icon in the dashboard
"My Receipt" - Print receipt - This does not exist in our system yet. So we need to create this from scratch - It will need to have - The test they are purchasing and the amount of the test - The customers name - The order ID - Must provide printer friendly option too
"My Orders" - This will have a list of orders - At the end of each order will be a status update of either "Test results" "Open order"
A graphic table format would be perfect. This will be linked to relevant results if they have been received. I have also attached a version of what the customer currently sees on our website. We know it is nasty ;) We are redesigning... but the information is there for this section to help design it with the right info. If the results are ready it will say in this list.
"Results Ready" will be a link to show those results once the customer has clicked the link, and the results will appear in the app, under the icons. There must be a printer friendly version too.
"My Results" Developer will sort this page out but we need the icon... It will be exactly like my orders but only show test results
"My Account" - This will be a place for them to update their personal information - Name, DOB, Address, Email Address
"My Inbox" - An inbox interface - Our way of contacting the customer for promotions we are running etc – We need a design of how this screen will appear. We also need the icon in the dashboard to have a notification on it if there are messages in the customers inbox. A little red 1, or circle with number of messages in the inbox.
"Customer Service" - This does not need to be designed because the web developer has this part under control, but we do need the icon in the dashboard
Icons appear along the top of app ( example - Mac icons/ iphone app icons) When the customer clicks an icon the content always appears below the icons
Here is more information for the icons and what should appear when each icon is clicked.
Screens to be designed –
Entry Page
Order A Test Page
Review Order Screen/Payment Screen - Show a lightbox that shows payment has been confirmed. Customer clicks close and are on the Confirmation Screen
VantiQor Dashboard - Screens mentioned in detail above
We can't wait to see your designs!
Please email any questions.
Hi all this is the first time we have used pixel harbor and understand the budget was too low for this project. We have now increased the budget to $2,000 and extended the deadline by another week
Hi all we are receiving some really great designs. I just added an example of the space that the web app will be going into... It is called "morvelapp.pdf"
Hi guys updated the brief. Hopefully this will help with the dashboard part of the design

```html
<!DOCTYPE html>
<html lang="en">
<head>
<meta charset="utf-8">
<title>VantiQor – Order A Test</title>
<link href="https://fonts.googleapis.com/css2?family=Open+Sans:wght@400;600;700&display=swap" rel="stylesheet">
<style>
  :root{
    --page:#ffffff;
    --brand-text:#2f2f2f;
    --header-olive:#8d9b55;
    --header-olive-dark:#7c8a47;
    --band-green:#8cb52e;
    --band-green-dark:#7da426;
    --select-text:#7b6a5c;
    --select-border:#b9b9b9;
    --row-text:#2f2f2f;
    --row-active:#86b226;
    --price:#4d2416;
    --icon:#6a6a6a;
    --divider:#dcdcdc;
    --stripe-1:#7ea12c;
    --stripe-2:#9cc23a;
    --stripe-3:#6f8f24;
    --stripe-4:#b5d35a;
  }
  *{box-sizing:border-box;margin:0;padding:0}
  html,body{width:692px;height:1200px;overflow:hidden;background:var(--page)}
  body{font-family:"Open Sans",sans-serif;position:relative}

  .brand{height:134px;display:flex;align-items:center;justify-content:center}
  .brand-name{font-size:50px;font-weight:600;color:var(--brand-text);letter-spacing:1px;line-height:1}

  .page-title{height:69px;background:linear-gradient(var(--header-olive),var(--header-olive-dark));
    color:#fff;font-size:34px;font-weight:400;text-align:center;line-height:69px}

  .category-bar{height:120px;background:linear-gradient(var(--band-green),var(--band-green-dark));padding:10px 42px 0}
  .category-label{color:#fff;font-size:22px;text-align:center;line-height:28px}
  .category-select{margin-top:8px;height:60px;background:#fff;border:2px solid var(--select-border);
    display:flex;align-items:center;justify-content:space-between}
  .category-value{font-size:30px;color:var(--select-text);padding-left:24px}
  .category-toggle{width:56px;height:56px;background:#eef3e2;border-left:2px solid var(--select-border);
    display:flex;align-items:center;justify-content:center}

  .test-list{list-style:none;margin-top:22px;padding:0 32px 0 23px}
  .test-row{height:80px;display:flex;align-items:center;border-bottom:2px solid var(--divider)}
  .test-row:last-child{border-bottom:none}
  .cart-icon{width:42px;height:34px;color:var(--icon);flex:none}
  .test-row.is-active .cart-icon{color:var(--row-active)}
  .row-divider{width:2px;height:52px;background:var(--divider);margin:0 20px 0 16px;flex:none}
  .test-name{flex:1;font-size:30px;color:var(--row-text);white-space:nowrap}
  .test-price{font-size:30px;color:var(--price)}
  .test-row.is-active .test-name,.test-row.is-active .test-price{color:var(--row-active)}

  .footer-stripes{position:absolute;left:0;bottom:0;width:692px;height:28px;display:flex}
  .footer-stripes span{height:100%}
</style>
</head>
<body>
<svg width="0" height="0" style="position:absolute">
  <symbol id="cart" viewBox="0 0 42 34">
    <path d="M2 4h7l5 18h20l5-13H12" fill="none" stroke="currentColor" stroke-width="3" stroke-linejoin="round" stroke-linecap="round"/>
    <path d="M15 12h20M16 17h17" stroke="currentColor" stroke-width="2.5"/>
    <circle cx="16" cy="29" r="3" fill="currentColor"/>
    <circle cx="31" cy="29" r="3" fill="currentColor"/>
  </symbol>
</svg>

<header class="brand">
  <span class="brand-name">VantiQor</span>
</header>

<h1 class="page-title">Order A Test</h1>

<section class="category-bar">
  <p class="category-label">Select A Category</p>
  <div class="category-select">
    <span class="category-value">Women's Health</span>
    <span class="category-toggle">
      <svg width="30" height="20" viewBox="0 0 30 20"><path d="M4 4l11 11L26 4" fill="none" stroke="#7da426" stroke-width="5"/></svg>
    </span>
  </div>
</section>

<ul class="test-list">
  <li class="test-row"><svg class="cart-icon"><use href="#cart"/></svg><span class="row-divider"></span><span class="test-name">Amenorrhea Profile</span><span class="test-price">$105.00</span></li>
  <li class="test-row is-active"><svg class="cart-icon"><use href="#cart"/></svg><span class="row-divider"></span><span class="test-name">CA-125</span><span class="test-price">$65.00</span></li>
  <li class="test-row"><svg class="cart-icon"><use href="#cart"/></svg><span class="row-divider"></span><span class="test-name">Calcium, Ionized, Serum</span><span class="test-price">$126.00</span></li>
  <li class="test-row"><svg class="cart-icon"><use href="#cart"/></svg><span class="row-divider"></span><span class="test-name">Calcium, Serum</span><span class="test-price">$45.00</span></li>
  <li class="test-row"><svg class="cart-icon"><use href="#cart"/></svg><span class="row-divider"></span><span class="test-name">Candida Antibodies,</span><span class="test-price">$175.00</span></li>
  <li class="test-row"><svg class="cart-icon"><use href="#cart"/></svg><span class="row-divider"></span><span class="test-name">Comprehensive Female</span><span class="test-price">$455.00</span></li>
  <li class="test-row"><svg class="cart-icon"><use href="#cart"/></svg><span class="row-divider"></span><span class="test-name">Female Cancer Screening</span><span class="test-price">$270.00</span></li>
  <li class="test-row"><svg class="cart-icon"><use href="#cart"/></svg><span class="row-divider"></span><span class="test-name">Female Ultimate Anti-Aging</span><span class="test-price">$600.00</span></li>
  <li class="test-row"><svg class="cart-icon"><use href="#cart"/></svg><span class="row-divider"></span><span class="test-name">Fibrinogen Activity</span><span class="test-price">$59.80</span></li>
  <li class="test-row"><svg class="cart-icon"><use href="#cart"/></svg><span class="row-divider"></span><span class="test-name">Candida Antibodies,</span><span class="test-price">$175.00</span></li>
</ul>

<footer class="footer-stripes">
  <span style="width:140px;background:var(--stripe-1)"></span>
  <span style="width:110px;background:var(--stripe-2)"></span>
  <span style="width:160px;background:var(--stripe-3)"></span>
  <span style="width:120px;background:var(--stripe-4)"></span>
  <span style="width:162px;background:var(--stripe-2)"></span>
</footer>
</body>
</html>
```